Torvane Email Signature Banners – Fabrication Capability Series

www.Torvane.com.au is an Australian engineering and fabrication company specialising in fabrication and welding of :
steel piping spools,
skids and frames,
small volume process steel tanks
and general steel fabrication
We require four distinct banner designs for use in Microsoft Lintaro email signatures. Each banner will highlight a specific capability while maintaining a consistent brand identity.
Deliverables
Four banners total:
Piping Spools Fabrication – focus on precision welding and stainless steel pipework
Skid & Frames Fabrication – highlight skid systems and structural frames
Small Steel Tanks Fabrication – show fabricated tanks and workshop craftsmanship
General Fabrication Solutions – broad steel fabrication theme for company-wide use
Dimensions: 600–700 px wide × 100 px high
Format: PNG (preferred), small file size prefered
Resolution: 72 dpi
Background: non-transparent, industrial or workshop setting
Text examples:
1. Piping Spools Fabrication
Option A: “Expert Fabrication Solutions for Process Piping”
Option B: “Precision Welding for Complex Systems”
Option C: “Delivering Quality in Every Spool”
Option D: “Engineered for Flow, Built for Strength”
2. Skid & Frames Fabrication
Option A: “Custom Engineered Modular Systems”
Option B: “Built Strong. Designed Smart.”
Option C: “Reliable Frames for Industrial Performance”
Option D: “Modular Fabrication for Seamless Integration”
3. Small Steel Tanks Fabrication
Option A: “Precision Built for Your Needs”
Option B: “Compact Strength. Proven Durability.”
Option C: “Fabricated for Performance and Longevity”
Option D: “Small Tanks. Big Reliability.”
4. General Fabrication Solutions
Option A: “Quality Craftsmanship, Proven Results”
Option B: “Your Partner in Precision Fabrication”
Option C: “Engineering Excellence in Every Weld”
Option D: “Australian Fabrication. Global Standards.”
Style Direction
Clean, professional, and engineering‑focused
Use Torvane brand colours
Blend photo realism with vector clarity (no heavy gradients)
Include subtle industrial textures or workshop imagery
Typography: bold sans‑serif, legible at small scale
Usage Context
These banners will appear at the bottom of staff email signatures via Lintaro Email Signature Tool for Microsoft 365, so clarity and fast loading are essential. No Logo is required in the banners.
Reference
Existing Torvane signature is attached. Colour palette to match the signature style and logo.
Target Market(s)
Engineering and construction companies,
Industry/Entity Type
Engineering fabrication design
Look and feel

```html
<!DOCTYPE html>
<html lang="en">
<head>
<meta charset="utf-8">
<title>Fabrication Capability Series – Email Signature Banners</title>
<link rel="preconnect" href="https://fonts.googleapis.com">
<link href="https://fonts.googleapis.com/css2?family=Poppins:wght@400;500;700&display=swap" rel="stylesheet">
<style>
  :root {
    --page-bg: #ffffff;
    --navy: #0b1726;
    --accent-blue: #2f9fe6;
    --title-white: #ffffff;
    --folio: #333a44;
  }
  * { box-sizing: border-box; margin: 0; padding: 0; }
  html, body {
    width: 1200px;
    height: 973px;
    overflow: hidden;
    background: var(--page-bg);
  }
  .sheet {
    position: relative;
    width: 1200px;
    height: 973px;
    background: var(--page-bg);
    font-family: "Poppins", Arial, sans-serif;
  }
  .banner {
    position: absolute;
    left: 100px;
    width: 1000px;
    height: 167px;
    background: var(--navy);
    overflow: hidden;
  }
  .banner--tanks   { top: 105px; }
  .banner--spools  { top: 312px; }
  .banner--skids   { top: 502px; }
  .banner--general { top: 702px; }

  .banner__photo {
    position: absolute;
    top: 0;
    right: 0;
    height: 100%;
  }
  .banner--tanks .banner__photo {
    width: 460px;
    background: linear-gradient(100deg, #1c2430 0%, #2e3440 35%, #5a2a22 62%, #9a3a2c 80%, #3b3f48 100%);
  }
  .banner--spools .banner__photo {
    width: 500px;
    background: linear-gradient(180deg, #6d7f99 0%, #3f5b86 40%, #27406a 65%, #8fa3bd 100%);
  }
  .banner--skids .banner__photo {
    width: 460px;
    background: linear-gradient(180deg, #9aa1a8 0%, #6a7078 45%, #3d4248 75%, #5b6067 100%);
  }
  .banner--general .banner__photo {
    width: 420px;
    background: radial-gradient(circle at 60% 70%, #f0a04a 0%, #9a5a2c 18%, #1f4a66 45%, #0e2234 80%);
  }

  .banner__panel {
    position: absolute;
    top: 0;
    left: 0;
    height: 100%;
  }

  .banner__text {
    position: absolute;
    left: 35px;
    top: 38px;
  }
  .banner__title {
    font-weight: 700;
    font-size: 33px;
    line-height: 1.2;
    color: var(--title-white);
    letter-spacing: -0.3px;
    white-space: nowrap;
  }
  .banner__tagline {
    margin-top: 14px;
    font-weight: 500;
    font-size: 16px;
    line-height: 1.2;
    color: var(--accent-blue);
    white-space: nowrap;
  }

  .folio {
    position: absolute;
    left: 1106px;
    top: 907px;
    font-size: 13px;
    font-weight: 400;
    color: var(--folio);
  }
</style>
</head>
<body>
<main class="sheet">

  <section class="banner banner--tanks">
    <div class="banner__photo" role="img" aria-label="Workers in hard hats inspecting large fabricated steel tanks in a workshop"></div>
    <svg class="banner__panel" width="660" height="167" viewBox="0 0 660 167" aria-hidden="true">
      <polygon points="0,0 558,0 625,83.5 558,167 0,167" fill="var(--navy)"/>
    </svg>
    <div class="banner__text">
      <h2 class="banner__title">SMALL STEEL TANKS</h2>
      <p class="banner__tagline">Compact Strength. Proven Durability.</p>
    </div>
  </section>

  <section class="banner banner--spools">
    <div class="banner__photo" role="img" aria-label="Stacks of steel pipe spools in a fabrication hall"></div>
    <svg class="banner__panel" width="640" height="167" viewBox="0 0 640 167" aria-hidden="true">
      <polygon points="0,0 525,0 592,83.5 525,167 0,167" fill="var(--navy)"/>
    </svg>
    <div class="banner__text">
      <h2 class="banner__title">PIPING SPOOLS FABRICATION</h2>
      <p class="banner__tagline">Precision Welding for Complex Systems</p>
    </div>
  </section>

  <section class="banner banner--skids">
    <div class="banner__photo" role="img" aria-label="Industrial skid with steel frames and pipework in a plant"></div>
    <svg class="banner__panel" width="640" height="167" viewBox="0 0 640 167" aria-hidden="true">
      <polygon points="0,0 560,0 610,83.5 560,167 0,167" fill="var(--navy)"/>
    </svg>
    <div class="banner__text">
      <h2 class="banner__title">SKID &amp; FRAMES FABRICATION</h2>
      <p class="banner__tagline">Built Strong. Designed Smart.</p>
    </div>
  </section>

  <section class="banner banner--general">
    <div class="banner__photo" role="img" aria-label="Welder at work with sparks flying in a steel workshop"></div>
    <svg class="banner__panel" width="700" height="167" viewBox="0 0 700 167" aria-hidden="true">
      <polygon points="0,0 580,0 680,83.5 580,167 0,167" fill="var(--navy)"/>
    </svg>
    <div class="banner__text">
      <h2 class="banner__title">GENERAL FABRICATION SOLUTIONS</h2>
      <p class="banner__tagline">Engineering Excellence in Every Weld</p>
    </div>
  </section>

  <p class="folio">C 72</p>
</main>
</body>
</html>
```